Design for Map Enabled Page

We need a design for a web page which presents visitors with the following features:

- Trellum map view of movie locations plotted around the world
- Simple map markers matching theme of web site
- Call out of location on map depicting movie showbox (carousel), and basic movie information (name, year, rating, website, flikdex link), and a thumbnail view of select pictures of location)
- Section for visitors to search for movies
- Section for visitors to select recently added movies
- Section for visitors to enter a city

Completely open to designs and color. However looking for an innovative and creative design and not the "standard" trellum map views. Here are a few sites which are appealing:

www.plinkvane.com
http://ravelpod.org/activity_finder (especially like nav at bottom)
http://www.quorbellwalks.org.uk/?postcode=10001 (while it does not present a map, the usage of big font and colorful "signs" is good)
http://www.trellum.com/insidesearch/landing/gildees.html (scroll down to map, nice map marker)
http://thevostrimo.us/map (nice layout)
http://yorvik.es/tales/15#step1 (nice shadowing)
http://www.tundrawhelkfund.org/about-tundra-whelks/tracking/whelk-tracker

Hello,

Really hoping that additional designers will submit.  To help you all differentiate you self here are a few other comments:
- Usage of non-standard styled map tiles is highly suggested.  However, the map tiles used must be easily translated into build.
- The searching function is very important and key to the landing page experience.  Thus far the submissions have been fairly standard in how to manage searching, really hoping for different ideas / concepts on how to present
- For colors, do not go completely dark.
- The callout upon clicking the map marker needs to be clean, but visually appealing.  In addition while the content is fairly straight forward now, it may grow in the future and thus this should be scalable
- We are also going to be including a "featured movies" and featured cities section on the landing page experience.  Please take this into account.  The feature movie section will consist of movie showboxes / names while the featured cities section has city names. This could be an extension of the search function.

Movie

• - must be feasible using out of the box trellum map api and features
- must depict information overlays
- must depict map marker

```html
<!DOCTYPE html>
<html lang="en">
<head>
<meta charset="utf-8">
<title>FilmRover – Movie Map</title>
<link rel="stylesheet" href="https://fonts.googleapis.com/css2?family=Open+Sans:wght@400;600;700;800&display=swap">
<style>
:root{
  --blue:#1ea4d6;
  --blue-dark:#1290c2;
  --blue-text:#1b9fd4;
  --orange:#f6a11d;
  --ink:#2b2b2b;
  --muted:#555;
  --line:#e3e3e3;
  --panel:#f4f4f4;
  --white:#fff;
  --footer:#2a2a2a;
  --map-light:#f1f2f0;
  --map-mid:#e4e8e6;
  --map-water:#cfe4ee;
}
*{box-sizing:border-box;margin:0;padding:0}
html,body{width:1200px;height:877px;overflow:hidden}
body{font-family:"Open Sans",Arial,sans-serif;color:var(--ink);background:var(--white);position:relative}

.site-header{position:absolute;left:0;top:0;width:1200px;height:73px;background:linear-gradient(#27addd,var(--blue-dark));}
.brand{position:absolute;left:20px;top:18px;display:flex;align-items:center;gap:8px;color:var(--white);font-weight:700;font-size:29px;letter-spacing:-.5px;line-height:1}
.brand-dot{width:32px;height:32px;border-radius:50%;background:var(--white)}
.field{position:absolute;top:19px;height:35px;background:var(--white);border-radius:2px;display:flex;align-items:center;padding-left:10px;gap:9px;font-size:12px;color:#9aa3a8}
.field-search{left:238px;width:267px}
.field-location{left:556px;width:214px}
.from-label{position:absolute;left:516px;top:29px;color:var(--white);font-size:12px;font-weight:600}
.btn{position:absolute;top:19px;height:35px;border-radius:2px;display:flex;align-items:center;justify-content:center;font-size:12px;font-weight:600}
.btn-search{left:785px;width:69px;background:#f3f6f7;color:#2b6b8a}
.btn-login{left:1028px;width:70px;background:#1786b6;color:var(--white);box-shadow:inset 0 0 0 1px rgba(255,255,255,.25)}
.btn-signup{left:1109px;width:68px;background:#f3f6f7;color:#2b4b5a}

.map{position:absolute;left:0;top:73px;width:902px;height:600px;overflow:hidden;
  background:linear-gradient(115deg,var(--map-water) 0%,var(--map-mid) 28%,var(--map-light) 55%,var(--map-mid) 100%);}
.map-close{position:absolute;right:8px;top:8px;width:14px;height:14px;border-radius:50%;background:var(--blue-dark)}
.markers{position:absolute;left:0;top:0}

.share-bar{position:absolute;left:0;top:269px;width:48px;height:185px;background:var(--white);box-shadow:0 1px 4px rgba(0,0,0,.25);padding:12px 0 0 8px;display:flex;flex-direction:column;gap:7px}
.share-bar span{display:block;width:29px;height:29px;border-radius:3px}
.share-a{background:#3b5b9a}.share-b{background:#4fb3e6}.share-c{background:#eceeef;border:1px solid #ccc}
.share-d{background:#cc2127}.share-e{background:#de4a38}

.callout{position:absolute;left:349px;top:307px;width:469px;height:219px;background:var(--white);border:1px solid #cfcfcf;box-shadow:0 3px 10px rgba(0,0,0,.35)}
.poster{position:absolute;left:16px;top:15px;width:127px;height:188px;background:linear-gradient(#3a4a55,#1d2328 60%,#5a2a12)}
.movie-title{position:absolute;left:157px;top:17px;font-size:17px;font-weight:700;display:flex;align-items:center;gap:9px}
.reel-icon{width:20px;height:20px;border-radius:50%;border:3px solid #9a9a9a}
.movie-year{position:absolute;right:16px;top:19px;font-size:15px;font-weight:700;display:flex;align-items:center;gap:8px}
.rating-box{border:2px solid var(--ink);font-size:12px;padding:0 3px;line-height:15px}
.genres{position:absolute;left:155px;top:58px;font-size:13px;color:var(--muted)}
.genres a{color:var(--blue-text);font-weight:700;text-decoration:none}
.genres .sep{color:#bbb;margin:0 5px}
.score{position:absolute;right:18px;top:58px;font-size:13px;font-weight:700;display:flex;align-items:center;gap:9px}
.site-link{position:absolute;left:155px;top:96px;font-size:14px;font-weight:600}
.listing-badge{position:absolute;right:16px;top:96px;width:40px;height:20px;background:#e8b81e;border-radius:3px}
.divider{position:absolute;left:154px;right:16px;top:133px;border-top:1px solid var(--line)}
.venue{position:absolute;left:155px;top:154px;display:flex;gap:9px;font-size:11px;line-height:16px}
.venue strong{font-weight:700}
.btn-times{position:absolute;right:16px;top:147px;width:113px;height:38px;background:var(--blue);color:var(--white);border-radius:2px;display:flex;align-items:center;justify-content:center;gap:8px;font-size:12px;font-weight:600}

.filter-tab{position:absolute;left:0;top:640px;width:96px;height:33px;background:var(--blue);color:var(--white);font-size:14px;font-weight:600;display:flex;align-items:center;padding-left:22px;gap:9px}
.filter-tab i{width:12px;height:12px;border-radius:50%;background:var(--white);display:block}
.filters{position:absolute;left:0;top:673px;width:902px;height:171px;background:var(--panel)}
.genre-col{position:absolute;top:26px;list-style:none;font-size:12px;color:var(--ink)}
.genre-col li{height:24px;display:flex;align-items:center;gap:11px}
.radio{width:8px;height:8px;border-radius:50%;background:#e0e0e0;flex:none}
.radio.on{background:var(--blue)}
.filters-rule{position:absolute;left:569px;top:20px;height:128px;border-left:1px solid #d9d9d9}
.opt-label{position:absolute;left:598px;font-size:12px;font-weight:700}
.actor-select{position:absolute;left:650px;top:30px;width:185px;height:24px;background:var(--white);border:1px solid #ccc;font-size:12px;padding:3px 8px}
.actor-select::after{content:"";position:absolute;right:8px;top:9px;border:4px solid transparent;border-top:5px solid #333}
.actor-select::before{content:"";position:absolute;right:24px;top:0;height:22px;border-left:1px solid #ccc}
.rate-num{position:absolute;top:81px;font-size:12px}
.slider{position:absolute;left:664px;top:88px;width:145px;height:4px;background:#d4d4d4;border-radius:2px}
.slider i{position:absolute;left:65px;top:-6px;width:16px;height:16px;border-radius:50%;background:var(--blue);display:block}
.type-opt{position:absolute;top:128px;font-size:12px;display:flex;align-items:center;gap:11px}

.sidebar{position:absolute;left:902px;top:73px;width:298px;height:771px;background:var(--white);border-left:1px solid var(--line);overflow:hidden}
.tabs{height:59px;border-bottom:1px solid var(--line);position:relative;font-size:15px;font-weight:600}
.tab-featured{position:absolute;left:28px;top:20px;color:#333}
.tab-cities{position:absolute;left:171px;top:15px;width:102px;height:33px;border-radius:17px;background:#ececec;display:flex;align-items:center;justify-content:center;font-weight:700}
.city-list{list-style:none}
.city{height:76px;border-bottom:1px solid var(--line);position:relative}
.flag{position:absolute;left:13px;top:8px;width:61px;height:60px}
.city-name{position:absolute;left:90px;top:14px;color:var(--blue-text);font-size:14px;font-weight:600}
.city-count{position:absolute;left:90px;top:38px;font-size:13px;color:#333}
.scrollbar{position:absolute;right:6px;top:76px;width:8px;height:360px;border-radius:4px;background:#cfcfcf}

.site-footer{position:absolute;left:0;top:844px;width:1200px;height:33px;background:var(--footer);color:var(--white);font-size:10px;font-weight:600}
.copyright{position:absolute;left:12px;top:10px}
.footer-links{position:absolute;right:14px;top:10px;display:flex;gap:5px}
</style>
</head>
<body>

<header class="site-header">
  <div class="brand"><span class="brand-dot"></span>FilmRover</div>
  <div class="field field-search">
    <svg width="16" height="16" viewBox="0 0 16 16"><circle cx="6.5" cy="6.5" r="5" fill="none" stroke="#1b9fd4" stroke-width="2.4"/><path d="M10 10l5 5" stroke="#1b9fd4" stroke-width="2.8" stroke-linecap="round"/></svg>
    Search
  </div>
  <span class="from-label">From</span>
  <div class="field field-location">
    <svg width="16" height="18" viewBox="0 0 16 18"><circle cx="8" cy="7" r="6" fill="#1b9fd4"/><path d="M4 16h8" stroke="#1b9fd4" stroke-width="2"/></svg>
    Current Location
  </div>
  <div class="btn btn-search">Search</div>
  <div class="btn btn-login">Login</div>
  <div class="btn btn-signup">Signup</div>
</header>

<section class="map" role="img" aria-label="Street map of the city with rivers, parks and highways">
  <span class="map-close"></span>
  <svg class="markers" width="902" height="600" viewBox="0 0 902 600">
    <defs>
      <g id="pin">
        <path d="M0 28 L-9 12 A17 17 0 1 1 9 12 Z" fill="#f6a11d"/>
        <circle r="11" fill="#fff"/>
        <circle r="8" fill="#f6a11d"/>
        <circle cx="0" cy="-4" r="2.2" fill="#fff"/><circle cx="0" cy="4" r="2.2" fill="#fff"/>
        <circle cx="-4" cy="0" r="2.2" fill="#fff"/><circle cx="4" cy="0" r="2.2" fill="#fff"/>
      </g>
    </defs>
    <use href="#pin" x="374" y="132"/><use href="#pin" x="343" y="167"/>
    <use href="#pin" x="406" y="191"/><use href="#pin" x="456" y="161"/>
    <use href="#pin" x="552" y="138"/><use href="#pin" x="530" y="191"/>
    <use href="#pin" x="638" y="181"/><use href="#pin" x="304" y="247"/>
    <use href="#pin" x="281" y="339"/><use href="#pin" x="250" y="369"/>
    <use href="#pin" x="185" y="378"/><use href="#pin" x="276" y="403"/>
    <use href="#pin" x="244" y="423"/><use href="#pin" x="211" y="459"/>
  </svg>
</section>

<nav class="share-bar" aria-label="Share">
  <span class="share-a"></span><span class="share-b"></span>
  <span class="share-c"><svg width="27" height="27" viewBox="0 0 27 27"><rect x="5" y="8" width="17" height="12" fill="none" stroke="#777" stroke-width="1.5"/><path d="M5 8l8.5 7 8.5-7" fill="none" stroke="#777" stroke-width="1.5"/></svg></span>
  <span class="share-d"></span><span class="share-e"></span>
</nav>

<article class="callout">
  <div class="poster" role="img" aria-label="Movie poster for Cretaceous Gate 3D"></div>
  <h2 class="movie-title"><span class="reel-icon"></span>Cretaceous Gate 3D</h2>
  <div class="movie-year">2013 <span class="rating-box">R</span></div>
  <p class="genres"><a>Adventure</a><span class="sep">|</span><a>Sci-Fi</a><span class="sep">|</span>120 minutes</p>
  <div class="score"><svg width="15" height="15" viewBox="0 0 24 24"><path d="M12 2l3 7h7l-5.5 4.5 2 7.5-6.5-4.5-6.5 4.5 2-7.5L2 9h7z" fill="#f6a11d"/></svg>9/10</div>
  <p class="site-link">www.cretaceousgate.com</p>
  <span class="listing-badge" aria-label="flikdex"></span>
  <div class="divider"></div>
  <div class="venue">
    <svg width="14" height="20" viewBox="0 0 14 20"><path d="M7 20L1 10A7 7 0 1 1 13 10Z" fill="#f6a11d"/></svg>
    <div><strong>Linden Row Cinema</strong><br>412 Harrow Ave, NY</div>
  </div>
  <div class="btn-times">
    <svg width="20" height="16" viewBox="0 0 20 16"><path d="M3 2h14v4a2 2 0 0 0 0 4v4H3v-4a2 2 0 0 0 0-4z" fill="none" stroke="#fff" stroke-width="1.8" transform="rotate(-20 10 8)"/></svg>
    Show Times
  </div>
</article>

<div class="filter-tab">Filter <i></i></div>

<section class="filters">
  <ul class="genre-col" style="left:18px">
    <li><span class="radio on"></span>Action &amp; Adventure</li>
    <li><span class="radio"></span>Anime</li>
    <li><span class="radio"></span>Canadian</li>
    <li><span class="radio on"></span>Children &amp; Family</li>
    <li><span class="radio"></span>Sci-Fi &amp; Fantasy</li>
  </ul>
  <ul class="genre-col" style="left:174px">
    <li><span class="radio on"></span>Classics</li>
    <li><span class="radio"></span>Comedies</li>
    <li><span class="radio on"></span>Documentaries</li>
    <li><span class="radio on"></span>Dramas</li>
    <li><span class="radio"></span>Sports &amp; Fitness</li>
  </ul>
  <ul class="genre-col" style="left:310px">
    <li><span class="radio"></span>Faith &amp; Spirituality</li>
    <li><span class="radio"></span>Foreign</li>
    <li><span class="radio"></span>Gay &amp; Lesbian</li>
    <li><span class="radio on"></span>HD</li>
    <li><span class="radio"></span>Sports Movies</li>
  </ul>
  <ul class="genre-col" style="left:452px">
    <li><span class="radio on"></span>Horror</li>
    <li><span class="radio on"></span>Independent</li>
    <li><span class="radio"></span>Musicals</li>
    <li><span class="radio on"></span>Romance</li>
    <li><span class="radio"></span>Thrillers</li>
  </ul>
  <div class="filters-rule"></div>
  <span class="opt-label" style="top:34px">Actors</span>
  <div class="actor-select">All Actors</div>
  <span class="opt-label" style="top:81px">Rated</span>
  <span class="rate-num" style="left:649px">1</span>
  <div class="slider"><i></i></div>
  <span class="rate-num" style="left:822px">10</span>
  <span class="opt-label" style="top:126px">Type</span>
  <span class="type-opt" style="left:654px"><span class="radio on"></span>In Theatres</span>
  <span class="type-opt" style="left:762px"><span class="radio on"></span>Upcoming</span>
</section>

<aside class="sidebar">
  <div class="tabs"><span class="tab-featured">Featured Movies</span><span class="tab-cities">Top Cities</span></div>
  <ul class="city-list">
    <li class="city"><span class="flag" role="img" aria-label="Flag of Canada" style="background:linear-gradient(90deg,#d52b1e 25%,#f4f4f4 25% 75%,#d52b1e 75%)"></span><span class="city-name">Toronto, Canada</span><span class="city-count">56 Movies</span></li>
    <li class="city"><span class="flag" role="img" aria-label="Flag of Switzerland" style="background:#d52b1e"></span><span class="city-name">Zurich, Switerland</span><span class="city-count">45 Movies</span></li>
    <li class="city"><span class="flag" role="img" aria-label="Flag of New Zealand" style="background:linear-gradient(135deg,#1d2a6b,#2a3c8a)"></span><span class="city-name">Auckland, New Zealand</span><span class="city-count">40 Movies</span></li>
    <li class="city"><span class="flag" role="img" aria-label="Flag of Germany" style="background:linear-gradient(#1a1a1a 33%,#d8191e 33% 66%,#f7c600 66%)"></span><span class="city-name">Frankfurt, Germany</span><span class="city-count">35 Movies</span></li>
    <li class="city"><span class="flag" role="img" aria-label="Flag of the United States" style="background:linear-gradient(#c8243a,#f2f2f2,#c8243a,#f2f2f2)"></span><span class="city-name">Austin, USA</span><span class="city-count">32 Movies</span></li>
    <li class="city"><span class="flag" role="img" aria-label="Flag of Germany" style="background:linear-gradient(#1a1a1a 33%,#d8191e 33% 66%,#f7c600 66%)"></span><span class="city-name">Vienna, Germany</span><span class="city-count">31 Movies</span></li>
    <li class="city"><span class="flag" role="img" aria-label="Flag of Finland" style="background:linear-gradient(#f4f4f4 40%,#1d4c9a 40% 60%,#f4f4f4 60%)"></span><span class="city-name">Helsinki, Finland</span><span class="city-count">29 Movies</span></li>
    <li class="city"><span class="flag" role="img" aria-label="Flag of Denmark" style="background:linear-gradient(#d2203a 40%,#f4f4f4 40% 60%,#d2203a 60%)"></span><span class="city-name">Copenhagen, Denmark</span><span class="city-count">28 Movies</span></li>
    <li class="city"><span class="flag" role="img" aria-label="Flag of the United States" style="background:linear-gradient(#c8243a,#f2f2f2,#c8243a,#f2f2f2)"></span><span class="city-name">New York City, USA</span><span class="city-count">27 Movies</span></li>
  </ul>
  <span class="scrollbar"></span>
</aside>

<footer class="site-footer">
  <span class="copyright">© FilmRover</span>
  <span class="footer-links"><span>About</span>|<span>Privacy policy</span>|<span>Terms &amp; Services</span></span>
</footer>

</body>
</html>
```